Velundra Jobs portal

Velundra Jobs is a job portal connecting job seekers and companies offering part time jobs in the Mena region, starting in the UAE. We would like to see designs that use the color blue. We have attached images to give an idea what the website should look like. When a company posts a job the job seekers are not allowed to see which company has posted a job. There should also be a coinvex gateway. On the landing page we want a catching picture that we will send.

Target Market(s)

Students and promotional workers

Logo Text

Velundra Jobs

Coding

Coded - Design and coding required

Number of Pages Required

4 page

Font styles to use
Sans Serif

Colors
33a6d7
0692cd
85cae6

```html
<!DOCTYPE html>
<html lang="en">
<head>
<meta charset="utf-8">
<title>Velundra Jobs</title>
<link href="https://fonts.googleapis.com/css2?family=Ubuntu:wght@300;400;500&display=swap" rel="stylesheet">
<style>
  :root {
    --sky-light: #fbfbfb;
    --sky-edge: #e9e9e9;
    --brand-teal: #4fc3c6;
    --brand-blue: #3a66b5;
    --btn-top: #3fb2e2;
    --btn-bottom: #1f8fc9;
    --btn-alt-top: #0aa0da;
    --btn-alt-bottom: #0380c0;
    --btn-border: #1a78ad;
    --text-main: #555555;
    --text-sub: #333333;
    --skyline: #85cae6;
  }
  * { margin: 0; padding: 0; box-sizing: border-box; }
  html, body { width: 1200px; height: 1099px; overflow: hidden; }
  body {
    position: relative;
    font-family: "Ubuntu", sans-serif;
    background: radial-gradient(ellipse 60% 55% at 50% 45%, var(--sky-light) 0%, #f4f4f4 60%, var(--sky-edge) 100%);
  }
  .brand-mark {
    position: absolute;
    left: 520px; top: 237px;
    width: 160px; height: 160px;
    border-radius: 50%;
    background: var(--brand-teal);
  }
  .brand-name {
    position: absolute;
    left: 0; width: 1200px; top: 440px;
    text-align: center;
    font-size: 70px;
    font-weight: 400;
    color: var(--brand-blue);
    letter-spacing: -1px;
  }
  .role-buttons {
    position: absolute;
    top: 580px; left: 370px;
    display: flex; gap: 25px;
  }
  .role-button {
    width: 217px; height: 60px;
    border-radius: 9px;
    border: 1px solid var(--btn-border);
    color: #fff;
    font-size: 19px;
    font-weight: 500;
    display: flex; align-items: center; justify-content: center;
    background: linear-gradient(var(--btn-top), var(--btn-bottom));
    box-shadow: 0 10px 8px -8px rgba(0,0,0,0.35);
    text-decoration: none;
  }
  .role-button.seeker { background: linear-gradient(var(--btn-alt-top), var(--btn-alt-bottom)); }
  .jobs-count {
    position: absolute; left: 0; width: 1200px; top: 670px;
    text-align: center;
    font-size: 24px; font-weight: 300;
    color: var(--text-main);
    letter-spacing: -0.8px;
  }
  .tagline {
    position: absolute; left: 0; width: 1200px; top: 715px;
    text-align: center;
    font-size: 13px; font-weight: 300;
    color: var(--text-sub);
    letter-spacing: -0.3px;
  }
  .skyline {
    position: absolute; left: 0; bottom: 0;
    width: 1200px; height: 247px;
    background: linear-gradient(to bottom, rgba(133,202,230,0) 0%, rgba(133,202,230,0.6) 25%, var(--skyline) 45%);
  }
</style>
</head>
<body>
  <header class="brand">
    <div class="brand-mark" aria-hidden="true"></div>
    <h1 class="brand-name">Velundra Jobs</h1>
  </header>
  <nav class="role-buttons">
    <a class="role-button employer" href="#">Employer</a>
    <a class="role-button seeker" href="#">Job Seeker</a>
  </nav>
  <p class="jobs-count">Total number of  jobs there currently are on the website.</p>
  <p class="tagline">Number one platform connecting people with events companies</p>
  <div class="skyline" role="img" aria-label="Light blue city skyline silhouette along the bottom of the page"></div>
</body>
</html>
```